Product Designer Business Card

Small product design, engineering and prototyping firm in need of a clean, professional business card design. To support our 3D design and drawing services, we offer 3D printing, molding, and casting of plastics, silicones, resins, etc. Our logo can still be modified/changed if necessary. The red/orange color is preferred, but may be substituted with blue or green, potentially. Either way, the colour of the logo should be match/compliment colors used throughout the design. One thought is to have the logo/contact info on one side, with the other side describing services offered, like with a small icon of 3D printer, molding, casting, and computer with a 3D model on-screen.
Industry/Entity Type
Mechanical Engineering
Contact Information for Business Card
Company: Kelvar Design
Phone: 613-582-9047
Email: mark@kelvardesign.ca

```html
<!DOCTYPE html>
<html lang="en">
<head>
<meta charset="utf-8">
<title>Kelvar Design – Business Card</title>
<link href="https://fonts.googleapis.com/css2?family=Open+Sans:wght@400;600&display=swap" rel="stylesheet">
<style>
  :root {
    --page-bg: #3b3b3b;
    --card-bg: #161616;
    --accent-red: #e0242a;
    --text-white: #f2f2f2;
    --icon-fill: #2a2a2a;
  }
  * { box-sizing: border-box; margin: 0; padding: 0; }
  html, body {
    width: 1200px; height: 1021px; overflow: hidden;
    background: var(--page-bg);
    font-family: "Open Sans", Arial, sans-serif;
  }
  .card {
    position: absolute; left: 180px;
    width: 840px; height: 480px;
    background: var(--card-bg);
    box-shadow: 0 6px 18px rgba(0,0,0,.45);
  }
  .card--services { top: 20px; }
  .card--contact { top: 521px; }

  .brand { position: absolute; display: flex; align-items: center; gap: 16px; }
  .brand__dot { width: 46px; height: 46px; border-radius: 50%; background: var(--accent-red); }
  .brand__name { color: var(--text-white); font-weight: 600; font-size: 44px; letter-spacing: 4px; }
  .card--services .brand { left: 50%; top: 50%; transform: translate(-50%, -50%); }
  .card--contact .brand { left: 70px; top: 60px; }

  .service { position: absolute; width: 140px; text-align: center; }
  .service__icon { display: block; width: 100px; height: 90px; margin: 0 auto 8px; background: var(--icon-fill); border-radius: 4px; }
  .service__label { color: var(--accent-red); font-size: 19px; }
  .service--printing { left: 70px; top: 40px; }
  .service--molding { left: 50px; top: 250px; }
  .service--casting { right: 50px; top: 110px; }
  .service--model { right: 80px; top: 300px; }

  .contact-list { position: absolute; left: 70px; bottom: 70px; list-style: none; }
  .contact-list li { display: flex; align-items: center; gap: 12px; color: var(--text-white); font-size: 21px; line-height: 34px; }
  .contact-list svg { width: 18px; height: 18px; flex: none; }

  .person { position: absolute; right: 80px; bottom: 120px; text-align: right; }
  .person__name { color: var(--accent-red); font-weight: 600; font-size: 30px; }
  .person__role { color: var(--text-white); font-size: 21px; }
</style>
</head>
<body>
  <section class="card card--services">
    <div class="service service--printing">
      <span class="service__icon" role="img" aria-label="Line icon of a 3D printer"></span>
      <span class="service__label">3D Printing</span>
    </div>
    <div class="service service--molding">
      <span class="service__icon" role="img" aria-label="Line icon of a molding machine"></span>
      <span class="service__label">Molding</span>
    </div>
    <div class="brand">
      <span class="brand__dot"></span>
      <span class="brand__name">Kelvar Design</span>
    </div>
    <div class="service service--casting">
      <span class="service__icon" role="img" aria-label="Line icon of resin being poured into a mold"></span>
      <span class="service__label">Casting</span>
    </div>
    <div class="service service--model">
      <span class="service__icon" role="img" aria-label="Line icon of a computer showing a 3D model"></span>
      <span class="service__label">3d Model</span>
    </div>
  </section>

  <section class="card card--contact">
    <div class="brand">
      <span class="brand__dot"></span>
      <span class="brand__name">Kelvar Design</span>
    </div>
    <ul class="contact-list">
      <li>
        <svg viewBox="0 0 24 24" aria-hidden="true"><path fill="#e0242a" d="M6.6 10.8a15 15 0 0 0 6.6 6.6l2.2-2.2a1 1 0 0 1 1-.25 11.4 11.4 0 0 0 3.6.57 1 1 0 0 1 1 1V20a1 1 0 0 1-1 1A17 17 0 0 1 3 4a1 1 0 0 1 1-1h3.5a1 1 0 0 1 1 1c0 1.25.2 2.45.57 3.57a1 1 0 0 1-.25 1z"/></svg>
        613-582-9047
      </li>
      <li>
        <svg viewBox="0 0 24 24" aria-hidden="true"><rect x="2" y="5" width="20" height="14" fill="none" stroke="#e0242a" stroke-width="2"/><path d="M2 5l10 8 10-8" fill="none" stroke="#e0242a" stroke-width="2"/></svg>
        mark@kelvardesign.ca
      </li>
      <li>
        <svg viewBox="0 0 24 24" aria-hidden="true"><g fill="none" stroke="#e0242a" stroke-width="2"><circle cx="12" cy="12" r="10"/><ellipse cx="12" cy="12" rx="4" ry="10"/><path d="M2 12h20"/></g></svg>
        www.kelvardesign.ca
      </li>
    </ul>
    <div class="person">
      <p class="person__name">Daniel Brooks</p>
      <p class="person__role">Owner</p>
    </div>
  </section>
</body>
</html>
```